Retail Jewelry Business Card Design Project

We are in need of a new business card design for a retail jewelry store. This store is in the business of fine jewelry including but not specific to bridal jewelry, diamonds, designer jewelry and watches.

This store has been in business for 20 years but continues to strive for a modern professional appeal. The main colors use for this business are a royal blue, white and silver.

Target Market(s)

Target market is ages 18-50

Industry/Entity Type

Jewelry

Requirements
Must have
• Sales Person Name
Sales Person Email Address

Store Address
Store Phone
Website

Standard business card size. No odd shapes or sizes.
Nice to have
• Overall modern feel for card.

We have thought that a design with a nice feature of the logo on the back of the card would be nice but open to ideas.
Should not have
• No specific images of jewelry should be used.

```html
<!DOCTYPE html>
<html lang="en">
<head>
<meta charset="utf-8">
<title>Marlow Reed Fine Jewelry – Business Cards</title>
<link rel="stylesheet" href="https://fonts.googleapis.com/css2?family=Open+Sans:ital,wght@0,400;0,600;1,700&display=swap">
<style>
  :root {
    --royal: #2e3192;
    --lavender: #7471b3;
    --white: #ffffff;
    --backdrop: #e8e3dc;
    --label: #2b2b2b;
    --card-radius: 20px;
  }
  * { margin: 0; padding: 0; box-sizing: border-box; }
  html, body { width: 1200px; height: 788px; overflow: hidden; }
  body {
    position: relative;
    background: var(--backdrop);
    font-family: "Open Sans", Arial, sans-serif;
  }
  .view-label {
    position: absolute;
    width: 200px;
    margin-left: -100px;
    text-align: center;
    font-size: 21px;
    color: var(--label);
  }
  .card {
    position: absolute;
    width: 525px;
    height: 300px;
    border-radius: var(--card-radius);
    overflow: hidden;
    box-shadow: 0 4px 10px rgba(0,0,0,0.25);
  }
  .card--white { background: var(--white); }
  .card--royal { background: var(--royal); }
  .card--lavender { background: var(--lavender); }

  /* Front */
  .front-info {
    position: absolute;
    left: 255px; top: 0;
    width: 246px; height: 100%;
    background: var(--royal);
    color: var(--white);
  }
  .front-strip {
    position: absolute;
    right: 0; top: 0;
    width: 24px; height: 100%;
    background: var(--lavender);
  }
  .front-pointer {
    position: absolute;
    left: 255px; top: 133px;
    width: 20px; height: 22px;
  }
  .rep-name {
    position: absolute;
    left: 38px; top: 52px;
    font-size: 16px;
  }
  .contact-line {
    position: absolute;
    left: 38px;
    font-size: 12.5px;
    line-height: 17px;
  }
  .contact-line b { font-style: italic; font-weight: 700; }

  /* Wordmark */
  .wordmark {
    position: absolute;
    text-align: center;
    font-family: "Open Sans", Arial, sans-serif;
    font-weight: 600;
    line-height: 1.1;
  }
  .wordmark .name { display: block; }
  .wordmark .trade { display: block; letter-spacing: 2px; }
  .wordmark--small { left: 0; width: 255px; top: 122px; color: var(--royal); }
  .wordmark--small .name { font-size: 30px; }
  .wordmark--small .trade { font-size: 13px; margin-top: 4px; }
  .wordmark--large { left: 0; width: 100%; top: 72px; }
  .wordmark--large .name { font-size: 54px; }
  .wordmark--large .trade { font-size: 19px; margin-top: 8px; }
  .on-white { color: var(--royal); }
  .on-royal { color: var(--white); }
  .on-lavender { color: var(--royal); }

  .web {
    position: absolute;
    left: 0; width: 100%;
    text-align: center;
    font-size: 13px;
    letter-spacing: 2px;
    top: 259px;
  }
  .web.on-royal { color: var(--white); }
  .web.on-white { color: var(--royal); }
  .web.on-lavender { color: #1f1f4d; }
</style>
</head>
<body>

  <div class="view-label" style="left:320px; top:33px;">Front</div>
  <div class="view-label" style="left:896px; top:33px;">Back - 1</div>
  <div class="view-label" style="left:320px; top:404px;">Back - 2</div>
  <div class="view-label" style="left:896px; top:404px;">Back - 3</div>

  <!-- Front -->
  <section class="card card--white" style="left:55px; top:75px;">
    <div class="wordmark wordmark--small">
      <span class="name">Marlow Reed</span>
      <span class="trade">FINE JEWELRY</span>
    </div>
    <div class="front-info">
      <div class="rep-name">Daniel Reed Marlow</div>
      <div class="contact-line" style="top:123px;"><b>p</b> : 555-013-2468</div>
      <div class="contact-line" style="top:155px;"><b>e</b> : daniel@marlowreedjewelry.com</div>
      <div class="contact-line" style="top:187px;"><b>w</b> : www.marlowreedjewelry.com</div>
      <div class="contact-line" style="top:211px;">2280 Bayview Street<br>Harbor Point, FL 32499</div>
    </div>
    <svg class="front-pointer" viewBox="0 0 20 22" aria-hidden="true">
      <polygon points="0,0 20,11 0,22" fill="var(--white)"/>
    </svg>
    <div class="front-strip"></div>
  </section>

  <!-- Back 1 -->
  <section class="card card--white" style="left:621px; top:73px;">
    <div class="wordmark wordmark--large on-white">
      <span class="name">Marlow Reed</span>
      <span class="trade">FINE JEWELRY</span>
    </div>
    <div class="web on-white">www.marlowreedjewelry.com</div>
  </section>

  <!-- Back 2 -->
  <section class="card card--royal" style="left:54px; top:445px;">
    <div class="wordmark wordmark--large on-royal">
      <span class="name">Marlow Reed</span>
      <span class="trade">FINE JEWELRY</span>
    </div>
    <div class="web on-royal">www.marlowreedjewelry.com</div>
  </section>

  <!-- Back 3 -->
  <section class="card card--lavender" style="left:622px; top:445px;">
    <div class="wordmark wordmark--large on-lavender">
      <span class="name">Marlow Reed</span>
      <span class="trade">FINE JEWELRY</span>
    </div>
    <div class="web on-lavender">www.marlowreedjewelry.com</div>
  </section>

</body>
</html>
```